Larkfield Ridge Management

I need a professional website. My current website is larkfieldridgemanagement.com and I hate it. It was created with some AI tool very quickly because I needed a site up and running with no advanced notice. I’m open to all designs .. I trust you, the professionals will deliver the results I’m anxiously awaiting! :)

```html
<!DOCTYPE html>
<html lang="en">
<head>
<meta charset="utf-8">
<title>Larkfield Ridge Management — Homepage Options</title>
<link rel="stylesheet" href="https://fonts.googleapis.com/css2?family=Barlow:wght@600;700;800&family=Montserrat:wght@400;500;600&display=swap">
<style>
:root{
  --navy:#1d2a50;
  --navy-deep:#17223f;
  --red:#c0161f;
  --mist:#f1f1f1;
  --stone:#c6c6c8;
  --ink:#1b1b1b;
  --muted:#555;
  --board:#656a7a;
  --bar:#4a4a4a;
  --sec-bg:var(--mist);
  --sec-ink:var(--ink);
  --sec-muted:var(--muted);
  --step-bg:var(--navy);
  --step-fg:#fff;
  --foot-bg:var(--mist);
}
*{box-sizing:border-box;margin:0;padding:0}
html,body{width:747px;height:1200px;overflow:hidden}
body{background:var(--board);position:relative;font-family:"Montserrat",sans-serif;color:var(--ink)}
.page{position:absolute;top:23px;width:668px;height:2336px;transform:scale(.4942);transform-origin:0 0;overflow:hidden;background:#fff}
.page--a{left:33px}
.page--b{left:385px;--sec-bg:var(--navy);--sec-ink:#fff;--sec-muted:#e4e6ee;--step-bg:#d2d3d6;--step-fg:var(--navy);--foot-bg:var(--stone)}
.abs{position:absolute}
.center{left:0;width:668px;text-align:center}
.h2{font-family:"Barlow",sans-serif;font-weight:700;font-size:19px;letter-spacing:.2px;color:var(--ink)}
.rule{width:44px;height:2px;background:var(--red);left:312px}
.lead{font-size:7.2px;line-height:13px;color:var(--muted)}
.btn{display:flex;align-items:center;gap:7px;height:24px;padding:0 16px 0 12px;background:var(--red);color:#fff;font-size:7.6px;font-weight:600;letter-spacing:.2px;clip-path:polygon(0 0,calc(100% - 8px) 0,100% 50%,calc(100% - 8px) 100%,0 100%)}
.btn svg{width:10px;height:6px}
/* top bar */
.topbar{top:0;left:160px;width:508px;height:22px;background:var(--navy);clip-path:polygon(8px 0,100% 0,100% 100%,20px 100%);display:flex;align-items:center;gap:12px;padding-left:28px;color:#fff;font-size:7px}
.topbar .sep{opacity:.5}
.social{display:inline-flex;gap:5px}
.social i{width:9px;height:9px;border-radius:50%;background:#fff;opacity:.85}
.brand{top:14px;left:74px;display:flex;align-items:center;gap:5px;font-family:"Barlow",sans-serif;font-weight:700;font-size:9.5px;color:var(--navy);line-height:1.05;width:100px}
.brand .mark{width:12px;height:12px;background:var(--navy);flex:none}
.nav{top:36px;left:178px;display:flex;gap:22px;font-size:7.4px;color:#222}
.nav .on{color:var(--red)}
.nav-cta{top:30px;left:471px}
/* hero */
.hero-photo{top:60px;left:0;width:668px;height:312px;background:linear-gradient(180deg,#9fb4c8 0%,#b7bfc4 30%,#7d6f5c 55%,#4a4a48 80%,#363636 100%)}
.shape{top:0;left:0}
.hero-title{top:110px;font-family:"Barlow",sans-serif;font-weight:700;font-size:25px;color:#111}
.hero-title em{font-style:normal;color:var(--navy)}
.hero-title b{color:var(--red);font-weight:700}
.hero-sub{top:147px;font-size:8.2px;line-height:16px;color:#111;font-weight:500}
.hero-cta{top:197px;left:269px}
.explore{top:310px;left:314px;width:40px;height:40px;border-radius:50%;border:1px dashed rgba(255,255,255,.6);display:flex;align-items:center;justify-content:center;color:#fff;font-size:15px}
/* steps */
.steps-title{top:396px;color:var(--sec-ink)}
.steps{top:456px;left:74px;width:520px;display:flex;justify-content:space-between}
.step{width:130px;text-align:center}
.step .ic{width:54px;height:54px;border-radius:50%;background:var(--step-bg);margin:0 auto 16px;display:flex;align-items:center;justify-content:center}
.step .ic svg{width:28px;height:28px;fill:none;stroke:var(--step-fg);stroke-width:1.6;stroke-linecap:round;stroke-linejoin:round}
.step h3{font-size:7.2px;font-weight:600;color:var(--sec-ink);margin-bottom:6px}
.step p{font-size:6.8px;line-height:13px;color:var(--sec-muted)}
.steps-cta{top:598px;left:276px}
/* services */
.svc-title{top:690px}
.svc-lead{top:744px}
.cards{top:790px;left:80px;display:flex;gap:14px}
.card{position:relative;width:160px;height:176px}
.card .photo{position:absolute;top:6px;left:0;width:160px;height:152px}
.card .price{position:absolute;top:0;right:0;background:var(--red);color:#fff;font-size:7.4px;font-weight:600;padding:3px 6px;clip-path:polygon(6px 0,100% 0,100% 100%,0 100%)}
.card .label{position:absolute;bottom:0;left:0;width:152px;height:20px;background:var(--navy);color:#fff;font-size:8px;display:flex;align-items:center;justify-content:space-between;padding:0 22px 0 9px;clip-path:polygon(0 0,calc(100% - 10px) 0,100% 100%,0 100%)}
.card .label.hot{background:var(--red)}
.card .label svg{width:10px;height:6px}
.arrow{top:864px;font-size:16px;color:#222}
/* about */
.about-photo{top:1010px;left:0;width:668px;height:365px;background:linear-gradient(90deg,#cfcfcf,#e2e2e2 55%,#d3d3d3)}
.about-brand{top:1150px;left:90px;display:flex;align-items:center;gap:12px;font-family:"Barlow",sans-serif;font-weight:700;font-size:28px;line-height:1.05;color:var(--navy);width:240px}
.about-brand .mark{width:36px;height:36px;background:var(--navy);flex:none}
.about-h{top:1078px;left:344px;font-family:"Barlow",sans-serif;font-weight:700;font-size:18.5px;line-height:27px;color:#111}
.about-rule{top:1141px;left:344px;width:16px;height:2px;background:var(--red)}
.about-copy{top:1160px;left:344px;width:243px;font-size:6.9px;line-height:13.4px;color:#444;text-align:justify}
.about-copy p+p{margin-top:4px}
.about-cta{top:1287px;left:344px}
/* form */
.form-title{top:1416px}
.form-lead{top:1470px}
.field{left:100px;width:228px;height:26px;border:1px solid #bcbcbc;background:#f2f2f2;font-size:6px;color:#888;padding:9px 10px}
.field b{color:var(--red);font-weight:500}
.msg{top:1500px;left:340px;width:228px;height:97px}
.form-cta{top:1619px;left:287px}
/* expertise */
.exp-title{top:1683px}
.exp-lead{top:1738px;font-size:8.4px;line-height:16px;color:#555}
.exp-cta{top:1789px;left:276px}
.city{top:1770px;left:0;width:668px;height:420px;background:linear-gradient(180deg,#fff 0%,#e8ebee 6%,#a9b4b8 14%,#5f7a4c 30%,#4f6b3d 60%,#6a7558 100%)}
/* footer */
.foot-brand{top:2135px;left:0;width:668px;display:flex;justify-content:center;align-items:center;gap:7px;font-family:"Barlow",sans-serif;font-weight:700;font-size:15px;color:var(--navy)}
.foot-brand .mark{width:14px;height:14px;background:var(--navy)}
.foot-nav{top:2216px;left:176px;display:flex;gap:33px;font-size:7.4px;color:#222}
.contacts{top:2258px;left:80px;width:520px;display:flex}
.contact{display:flex;align-items:center;gap:9px;padding-right:16px;margin-right:16px;border-right:1px solid #c9c9c9}
.contact:last-child{border:0}
.contact .ci{width:34px;height:34px;border-radius:50%;background:var(--navy);display:flex;align-items:center;justify-content:center;flex:none}
.contact .ci svg{width:15px;height:15px;fill:#fff}
.contact small{display:block;font-size:6px;color:var(--red);font-weight:600}
.contact span{display:block;font-size:7.4px;color:#222;margin:3px 0}
.contact em{display:block;font-size:5.4px;color:#777;font-style:normal}
.copy{top:2316px;left:0;width:668px;height:20px;background:var(--bar);color:#eee;font-size:7px;display:flex;align-items:center;justify-content:center}
.page--b .foot-brand{top:2140px}
.page--b .foot-nav{top:2221px}
.page--b .contacts{top:2263px}
</style>
</head>
<body>

<!-- ===== Option A ===== -->
<div class="page page--a">
  <div class="abs topbar"><span>✆ +1-555-010-0148</span><span class="sep">/</span><span>✉ info@larkfieldridgemanagement.com</span><span class="sep">/</span><span>Follow Us:</span><span class="social"><i></i><i></i><i></i><i></i></span></div>
  <div class="abs brand"><span class="mark"></span><span>Larkfield Ridge Management</span></div>
  <nav class="abs nav"><span class="on">HOME</span><span>ABOUT US</span><span>SERVICES</span><span>BLOG</span><span>CONTACT US</span></nav>
  <div class="abs btn nav-cta">REQUEST A QUOTE <svg viewBox="0 0 10 6"><path d="M0 3h9M6 .5 9 3 6 5.5" stroke="#fff" fill="none"/></svg></div>

  <div class="abs hero-photo" role="img" aria-label="Photo of a hillside street lined with suburban houses under a cloudy sky"></div>
  <svg class="abs shape" width="668" height="650" aria-hidden="true">
    <polygon points="0,60 668,60 668,120 0,120" fill="#fff" opacity=".0"/>
    <polygon points="0,300 334,372 668,300 668,650 0,650" fill="var(--sec-bg)"/>
    <polygon points="0,282 334,355 668,282 668,294 334,366 0,294" fill="var(--red)"/>
    <polygon points="0,294 334,366 668,294 668,300 334,372 0,300" fill="var(--navy)"/>
  </svg>
  <h1 class="abs center hero-title">A TRUE <em>PARTNER,</em>NOT JUST A <b>VENDOR.</b></h1>
  <p class="abs center hero-sub">Larkfield Ridge Management delivers professional residential and commercial<br>property management throughout Northeast Ohio.</p>
  <div class="abs btn hero-cta">REQUEST A QUOTE <svg viewBox="0 0 10 6"><path d="M0 3h9M6 .5 9 3 6 5.5" stroke="#fff" fill="none"/></svg></div>
  <div class="abs explore">★</div>

  <h2 class="abs center h2 steps-title">HOW IT WORKS</h2>
  <div class="abs rule" style="top:432px"></div>
  <div class="abs steps">
    <div class="step"><div class="ic"><svg viewBox="0 0 28 28"><path d="M6 5c2 0 3 4 3 5s-2 1-1 3 3 5 5 6 2-1 3-1 5 1 5 3-2 3-4 3C11 24 4 17 4 9c0-2 1-4 2-4z"/><rect x="15" y="4" width="9" height="7" rx="1"/></svg></div><h3>SCHEDULE A CONSULTATION</h3><p>Tell us about your property and management goals.</p></div>
    <div class="step"><div class="ic"><svg viewBox="0 0 28 28"><path d="M4 14 14 5l10 9M7 12v11h14V12"/><rect x="11" y="16" width="6" height="7"/></svg></div><h3>PROPERTY EVALUATION</h3><p>We'll assess your property and recommend a management</p></div>
    <div class="step"><div class="ic"><svg viewBox="0 0 28 28"><path d="M14 23S4 17 4 10a5 5 0 0 1 10-1 5 5 0 0 1 10 1c0 7-10 13-10 13z"/></svg></div><h3>WE HANDLE EVERYTHING</h3><p>From marketing to maintenance, we take care of the day-to-day operations.</p></div>
    <div class="step"><div class="ic"><svg viewBox="0 0 28 28"><path d="M14 3l3 3h4v4l3 3-3 3v4h-4l-3 3-3-3H7v-4l-3-3 3-3V6h4z"/><path d="M10 14l3 3 5-6"/></svg></div><h3>YOU RECEIVE RESULTS</h3><p>Tell us about your property and management goals.</p></div>
  </div>
  <div class="abs btn steps-cta">REQUEST A QUOTE <svg viewBox="0 0 10 6"><path d="M0 3h9M6 .5 9 3 6 5.5" stroke="#fff" fill="none"/></svg></div>

  <h2 class="abs center h2 svc-title">STRATEGIC PROPERTY MANAGEMENT SOLUTIONS</h2>
  <div class="abs rule" style="top:726px"></div>
  <p class="abs center lead svc-lead">Our analysis demonstrates that effective property oversight originates from meticulous operational planning, transparent<br>communication channels, and data-driven performance metrics across every asset class.</p>
  <span class="abs arrow" style="left:52px">‹</span><span class="abs arrow" style="left:606px">›</span>
  <div class="abs cards">
    <div class="card"><div class="photo" role="img" aria-label="Photo of hands arranging papers on a wooden desk" style="background:linear-gradient(135deg,#6b5644,#c9b79f 55%,#8a7560)"></div><span class="price">$99.00</span><div class="label">Basic Service <svg viewBox="0 0 10 6"><path d="M0 3h9M6 .5 9 3 6 5.5" stroke="#fff" fill="none"/></svg></div></div>
    <div class="card"><div class="photo" role="img" aria-label="Photo of a lamp and an open book on a table" style="background:linear-gradient(160deg,#d9c7ad,#b69a78 60%,#2a2623)"></div><span class="price">$149.00</span><div class="label hot">Intermediate Service <svg viewBox="0 0 10 6"><path d="M0 3h9M6 .5 9 3 6 5.5" stroke="#fff" fill="none"/></svg></div></div>
    <div class="card"><div class="photo" role="img" aria-label="Photo of a laptop and vase of flowers on a desk" style="background:linear-gradient(135deg,#5e4a38,#a48a6e 50%,#d9d4cc)"></div><span class="price">$199.00</span><div class="label">Advanced Service <svg viewBox="0 0 10 6"><path d="M0 3h9M6 .5 9 3 6 5.5" stroke="#fff" fill="none"/></svg></div></div>
  </div>

  <div class="abs about-photo" role="img" aria-label="Faded photo of a bright modern interior"></div>
  <svg class="abs shape" width="668" height="1400" aria-hidden="true">
    <polygon points="0,1000 668,1000 668,1072 334,1014 0,1072" fill="#fff"/>
    <polygon points="0,1302 334,1368 668,1302 668,1400 0,1400" fill="#fff"/>
    <polygon points="0,1060 334,1002 668,1060 668,1068 334,1010 0,1068" fill="var(--navy)"/>
    <polygon points="0,1068 334,1010 668,1068 668,1073 334,1015 0,1073" fill="var(--red)"/>
    <polygon points="0,1298 334,1362 668,1298 668,1303 334,1367 0,1303" fill="var(--red)"/>
    <polygon points="0,1303 334,1367 668,1303 668,1311 334,1375 0,1311" fill="var(--navy)"/>
  </svg>
  <div class="abs about-brand"><span class="mark"></span><span>Larkfield Ridge Management</span></div>
  <h2 class="abs about-h">ABOUT OUR PROPERTY<br>MANAGEMENT SOLUTIONS</h2>
  <div class="abs about-rule"></div>
  <div class="abs about-copy"><p>Our organization delivers comprehensive property management solutions that optimize asset performance and tenant satisfaction. By integrating advanced analytics with proven operational frameworks, our specialists ensure each property achieves sustained value appreciation.</p><p>Drawing on decades of collective expertise, the team facilitates regulatory compliance, cost efficiency,&amp; proactive maintenance. This disciplined approach enables owners to preserve</p></div>
  <div class="abs btn about-cta">LEARN MORE <svg viewBox="0 0 10 6"><path d="M0 3h9M6 .5 9 3 6 5.5" stroke="#fff" fill="none"/></svg></div>

  <h2 class="abs center h2 form-title">REQUEST A TAILORED PROPOSAL</h2>
  <div class="abs rule" style="top:1452px"></div>
  <p class="abs center lead form-lead">Submit the form to initiate a consultative assessment and explore solutions aligned with your objectives.</p>
  <div class="abs field" style="top:1500px">Full Name <b>*</b></div>
  <div class="abs field" style="top:1535px">Email Address <b>*</b></div>
  <div class="abs field" style="top:1570px">Phone Number <b>*</b></div>
  <div class="abs field msg">Message <b>*</b></div>
  <div class="abs btn form-cta">SUBMIT NOW <svg viewBox="0 0 10 6"><path d="M0 3h9M6 .5 9 3 6 5.5" stroke="#fff" fill="none"/></svg></div>

  <div class="abs city" role="img" aria-label="Aerial photo of a leafy residential neighborhood with a city skyline in the distance"></div>
  <h2 class="abs center h2 exp-title">EXPERTISE ROOTED IN ASSET PRESERVATION</h2>
  <div class="abs rule" style="top:1720px"></div>
  <p class="abs center exp-lead">The organization applies rigorously tested frameworks and data-driven methodologies to safeguard property<br>value while elevating tenant experience.</p>
  <div class="abs btn exp-cta">REQUEST A QUOTE <svg viewBox="0 0 10 6"><path d="M0 3h9M6 .5 9 3 6 5.5" stroke="#fff" fill="none"/></svg></div>
  <svg class="abs shape" width="668" height="2336" aria-hidden="true">
    <polygon points="0,2158 334,2070 668,2158 668,2336 0,2336" fill="var(--foot-bg)"/>
    <polygon points="0,2146 334,2058 668,2146 668,2152 334,2064 0,2152" fill="var(--navy)"/>
    <polygon points="0,2152 334,2064 668,2152 668,2159 334,2071 0,2159" fill="var(--red)"/>
  </svg>
  <div class="abs foot-brand"><span class="mark"></span>Larkfield Ridge Management</div>
  <nav class="abs foot-nav"><span>HOME</span><span>ABOUT US</span><span>SERVICES</span><span>BLOG</span><span>CONTACT US</span></nav>
  <div class="abs contacts">
    <div class="contact"><span class="ci"><svg viewBox="0 0 16 16"><path d="M4 1c1 0 2 3 2 4s-1 1-.5 2 2 3 3 3.5 1-.5 2-.5 3 1 3 2-1 3-3 3C6 15 1 10 1 5c0-2 2-4 3-4z"/></svg></span><div><small>PHONE</small><span>+1-555-010-0148</span><em>CALL US</em></div></div>
    <div class="contact"><span class="ci"><svg viewBox="0 0 16 16"><path d="M1 4h14v9H1zM1 4l7 5 7-5" stroke="var(--navy)" stroke-width="1"/></svg></span><div><small>EMAIL</small><span>info@larkfieldridgemanagement.com</span><em>EMAIL US</em></div></div>
    <div class="contact"><span class="ci"><svg viewBox="0 0 16 16"><path d="M8 1a5 5 0 0 1 5 5c0 4-5 9-5 9S3 10 3 6a5 5 0 0 1 5-5zm0 3a2 2 0 1 0 0 4 2 2 0 0 0 0-4z"/></svg></span><div><small>ADDRESS</small><span>Lorem ipsum dolor 123</span><em>OFFICE</em></div></div>
  </div>
  <div class="abs copy">© 2026 Copyright - Larkfield Ridge Management LLC</div>
</div>

<!-- ===== Option B ===== -->
<div class="page page--b">
  <div class="abs topbar"><span>✆ +1-555-010-0148</span><span class="sep">/</span><span>✉ info@larkfieldridgemanagement.com</span><span class="sep">/</span><span>Follow Us:</span><span class="social"><i></i><i></i><i></i><i></i></span></div>
  <div class="abs brand"><span class="mark"></span><span>Larkfield Ridge Management</span></div>
  <nav class="abs nav"><span class="on">HOME</span><span>ABOUT US</span><span>SERVICES</span><span>BLOG</span><span>CONTACT US</span></nav>
  <div class="abs btn nav-cta">REQUEST A QUOTE <svg viewBox="0 0 10 6"><path d="M0 3h9M6 .5 9 3 6 5.5" stroke="#fff" fill="none"/></svg></div>

  <div class="abs hero-photo" role="img" aria-label="Photo of a hillside street lined with suburban houses under a cloudy sky"></div>
  <svg class="abs shape" width="668" height="650" aria-hidden="true">
    <polygon points="0,300 334,372 668,300 668,650 0,650" fill="var(--sec-bg)"/>
    <polygon points="0,282 334,355 668,282 668,294 334,366 0,294" fill="var(--red)"/>
    <polygon points="0,294 334,366 668,294 668,300 334,372 0,300" fill="var(--navy-deep)"/>
  </svg>
  <h1 class="abs center hero-title">A TRUE <em>PARTNER,</em>NOT JUST A <b>VENDOR.</b></h1>
  <p class="abs center hero-sub">Larkfield Ridge Management delivers professional residential and commercial<br>property management throughout Northeast Ohio.</p>
  <div class="abs btn hero-cta">REQUEST A QUOTE <svg viewBox="0 0 10 6"><path d="M0 3h9M6 .5 9 3 6 5.5" stroke="#fff" fill="none"/></svg></div>
  <div class="abs explore">★</div>

  <h2 class="abs center h2 steps-title">HOW IT WORKS</h2>
  <div class="abs rule" style="top:432px"></div>
  <div class="abs steps">
    <div class="step"><div class="ic"><svg viewBox="0 0 28 28"><path d="M6 5c2 0 3 4 3 5s-2 1-1 3 3 5 5 6 2-1 3-1 5 1 5 3-2 3-4 3C11 24 4 17 4 9c0-2 1-4 2-4z"/><rect x="15" y="4" width="9" height="7" rx="1"/></svg></div><h3>SCHEDULE A CONSULTATION</h3><p>Tell us about your property and management goals.</p></div>
    <div class="step"><div class="ic"><svg viewBox="0 0 28 28"><path d="M4 14 14 5l10 9M7 12v11h14V12"/><rect x="11" y="16" width="6" height="7"/></svg></div><h3>PROPERTY EVALUATION</h3><p>We'll assess your property and recommend a management</p></div>
    <div class="step"><div class="ic"><svg viewBox="0 0 28 28"><path d="M14 23S4 17 4 10a5 5 0 0 1 10-1 5 5 0 0 1 10 1c0 7-10 13-10 13z"/></svg></div><h3>WE HANDLE EVERYTHING</h3><p>From marketing to maintenance, we take care of the day-to-day operations.</p></div>
    <div class="step"><div class="ic"><svg viewBox="0 0 28 28"><path d="M14 3l3 3h4v4l3 3-3 3v4h-4l-3 3-3-3H7v-4l-3-3 3-3V6h4z"/><path d="M10 14l3 3 5-6"/></svg></div><h3>YOU RECEIVE RESULTS</h3><p>Tell us about your property and management goals.</p></div>
  </div>
  <div class="abs btn steps-cta">REQUEST A QUOTE <svg viewBox="0 0 10 6"><path d="M0 3h9M6 .5 9 3 6 5.5" stroke="#fff" fill="none"/></svg></div>

  <h2 class="abs center h2 svc-title">STRATEGIC PROPERTY MANAGEMENT SOLUTIONS</h2>
  <div class="abs rule" style="top:726px"></div>
  <p class="abs center lead svc-lead">Our analysis demonstrates that effective property oversight originates from meticulous operational planning, transparent<br>communication channels, and data-driven performance metrics across every asset class.</p>
  <span class="abs arrow" style="left:52px">‹</span><span class="abs arrow" style="left:606px">›</span>
  <div class="abs cards">
    <div class="card"><div class="photo" role="img" aria-label="Photo of hands arranging papers on a wooden desk" style="background:linear-gradient(135deg,#6b5644,#c9b79f 55%,#8a7560)"></div><span class="price">$99.00</span><div class="label">Basic Service <svg viewBox="0 0 10 6"><path d="M0 3h9M6 .5 9 3 6 5.5" stroke="#fff" fill="none"/></svg></div></div>
    <div class="card"><div class="photo" role="img" aria-label="Photo of a lamp and an open book on a table" style="background:linear-gradient(160deg,#d9c7ad,#b69a78 60%,#2a2623)"></div><span class="price">$149.00</span><div class="label hot">Intermediate Service <svg viewBox="0 0 10 6"><path d="M0 3h9M6 .5 9 3 6 5.5" stroke="#fff" fill="none"/></svg></div></div>
    <div class="card"><div class="photo" role="img" aria-label="Photo of a laptop and vase of flowers on a desk" style="background:linear-gradient(135deg,#5e4a38,#a48a6e 50%,#d9d4cc)"></div><span class="price">$199.00</span><div class="label">Advanced Service <svg viewBox="0 0 10 6"><path d="M0 3h9M6 .5 9 3 6 5.5" stroke="#fff" fill="none"/></svg></div></div>
  </div>

  <div class="abs about-photo" role="img" aria-label="Faded photo of a bright modern interior"></div>
  <svg class="abs shape" width="668" height="1400" aria-hidden="true">
    <polygon points="0,1000 668,1000 668,1072 334,1014 0,1072" fill="#fff"/>
    <polygon points="0,1302 334,1368 668,1302 668,1400 0,1400" fill="#fff"/>
    <polygon points="0,1060 334,1002 668,1060 668,1068 334,1010 0,1068" fill="var(--navy)"/>
    <polygon points="0,1068 334,1010 668,1068 668,1073 334,1015 0,1073" fill="var(--red)"/>
    <polygon points="0,1298 334,1362 668,1298 668,1303 334,1367 0,1303" fill="var(--red)"/>
    <polygon points="0,1303 334,1367 668,1303 668,1311 334,1375 0,1311" fill="var(--navy)"/>
  </svg>
  <div class="abs about-brand"><span class="mark"></span><span>Larkfield Ridge Management</span></div>
  <h2 class="abs about-h">ABOUT OUR PROPERTY<br>MANAGEMENT SOLUTIONS</h2>
  <div class="abs about-rule"></div>
  <div class="abs about-copy"><p>Our organization delivers comprehensive property management solutions that optimize asset performance and tenant satisfaction. By integrating advanced analytics with proven operational frameworks, our specialists ensure each property achieves sustained value appreciation.</p><p>Drawing on decades of collective expertise, the team facilitates regulatory compliance, cost efficiency,&amp; proactive maintenance. This disciplined approach enables owners to preserve</p></div>
  <div class="abs btn about-cta">LEARN MORE <svg viewBox="0 0 10 6"><path d="M0 3h9M6 .5 9 3 6 5.5" stroke="#fff" fill="none"/></svg></div>

  <h2 class="abs center h2 form-title">REQUEST A TAILORED PROPOSAL</h2>
  <div class="abs rule" style="top:1452px"></div>
  <p class="abs center lead form-lead">Submit the form to initiate a consultative assessment and explore solutions aligned with your objectives.</p>
  <div class="abs field" style="top:1500px">Full Name <b>*</b></div>
  <div class="abs field" style="top:1535px">Email Address <b>*</b></div>
  <div class="abs field" style="top:1570px">Phone Number <b>*</b></div>
  <div class="abs field msg">Message <b>*</b></div>
  <div class="abs btn form-cta">SUBMIT NOW <svg viewBox="0 0 10 6"><path d="M0 3h9M6 .5 9 3 6 5.5" stroke="#fff" fill="none"/></svg></div>

  <div class="abs city" role="img" aria-label="Aerial photo of a leafy residential neighborhood with a city skyline in the distance"></div>
  <h2 class="abs center h2 exp-title">EXPERTISE ROOTED IN ASSET PRESERVATION</h2>
  <div class="abs rule" style="top:1720px"></div>
  <p class="abs center exp-lead">The organization applies rigorously tested frameworks and data-driven methodologies to safeguard property<br>value while elevating tenant experience.</p>
  <div class="abs btn exp-cta">REQUEST A QUOTE <svg viewBox="0 0 10 6"><path d="M0 3h9M6 .5 9 3 6 5.5" stroke="#fff" fill="none"/></svg></div>
  <svg class="abs shape" width="668" height="2336" aria-hidden="true">
    <polygon points="0,2162 334,2075 668,2162 668,2336 0,2336" fill="var(--foot-bg)"/>
    <polygon points="0,2150 334,2063 668,2150 668,2156 334,2069 0,2156" fill="var(--navy)"/>
    <polygon points="0,2156 334,2069 668,2156 668,2163 334,2076 0,2163" fill="var(--red)"/>
  </svg>
  <div class="abs foot-brand"><span class="mark"></span>Larkfield Ridge Management</div>
  <nav class="abs foot-nav"><span>HOME</span><span>ABOUT US</span><span>SERVICES</span><span>BLOG</span><span>CONTACT US</span></nav>
  <div class="abs contacts">
    <div class="contact"><span class="ci"><svg viewBox="0 0 16 16"><path d="M4 1c1 0 2 3 2 4s-1 1-.5 2 2 3 3 3.5 1-.5 2-.5 3 1 3 2-1 3-3 3C6 15 1 10 1 5c0-2 2-4 3-4z"/></svg></span><div><small>PHONE</small><span>+1-555-010-0148</span><em>CALL US</em></div></div>
    <div class="contact"><span class="ci"><svg viewBox="0 0 16 16"><path d="M1 4h14v9H1zM1 4l7 5 7-5" stroke="var(--navy)" stroke-width="1"/></svg></span><div><small>EMAIL</small><span>info@larkfieldridgemanagement.com</span><em>EMAIL US</em></div></div>
    <div class="contact"><span class="ci"><svg viewBox="0 0 16 16"><path d="M8 1a5 5 0 0 1 5 5c0 4-5 9-5 9S3 10 3 6a5 5 0 0 1 5-5zm0 3a2 2 0 1 0 0 4 2 2 0 0 0 0-4z"/></svg></span><div><small>ADDRESS</small><span>Lorem ipsum dolor 123</span><em>OFFICE</em></div></div>
  </div>
  <div class="abs copy">© 2026 Copyright - Larkfield Ridge Management LLC</div>
</div>

</body>
</html>
```